Premium Organic Ceremonial Matcha Green Tea - Product Label

Two Label Bag Sizes: 18x30cm and 17x24cm

Be EXTRA Creative.. please message me with any questions and I will respond quickly.

Target Market(s)

Health, Organic, Green Tea Matcha Drinkers

Industry/Entity Type

Product

Requirements
Must have
• Organic Matcha Green Tea
• Try to incorporate geometry in logo into design... not mandatory but preferred for branding.

```html
<!DOCTYPE html>
<html lang="en">
<head>
<meta charset="utf-8">
<title>Verdant Crest Ceremonial Matcha – Label Set</title>
<link href="https://fonts.googleapis.com/css2?family=Alfa+Slab+One&family=Cinzel:wght@600;700&family=Oswald:wght@500;600&family=Open+Sans:ital,wght@1,600;1,700&family=Cormorant+Garamond:ital,wght@1,600&display=swap" rel="stylesheet">
<style>
  :root{
    --stage:#9a9a9a;
    --paper:#f3f4f1;
    --paper-hex:#e6ebe3;
    --ink:#141414;
    --leaf:#2f8a3a;
    --leaf-deep:#1f6b2a;
    --field:#4f8f3e;
    --field-dark:#2d5c24;
    --night:#2d2b36;
    --night-soft:#3a3744;
    --cream:#f2efe6;
    --gold:#b59a55;
    --badge:#2c6b34;
    --badge-ring:#f5f5f0;
  }
  *{margin:0;padding:0;box-sizing:border-box}
  html,body{width:1200px;height:900px;overflow:hidden}
  body{background:var(--stage);position:relative;font-family:"Open Sans",sans-serif}

  .label{position:absolute;top:247px;width:302px;height:443px;overflow:hidden}
  .label--classic{left:124px;background:var(--paper)}
  .label--night{left:435px;background:var(--night)}
  .label--modern{left:748px;background:var(--paper)}

  .pattern-zone{position:absolute;left:0;top:0;width:100%;height:150px;background:linear-gradient(var(--paper-hex),var(--paper))}
  .label--night .pattern-zone{background:linear-gradient(var(--night-soft),var(--night))}

  .brand{position:absolute;top:80px;left:0;width:100%;display:flex;justify-content:center;align-items:center;gap:7px}
  .brand__dot{width:14px;height:14px;border-radius:50%;background:var(--leaf)}
  .brand__name{font-family:"Cormorant Garamond",serif;font-style:italic;font-weight:600;font-size:24px;color:var(--field-dark)}
  .label--night .brand__name{color:var(--gold)}

  .scene{position:absolute;left:0;width:100%}
  .scene--hills{top:215px;height:228px;background:linear-gradient(rgba(243,244,241,0) 0%,var(--field) 22%,var(--field-dark) 100%)}
  .scene--bowl{left:150px;top:320px;width:165px;height:123px;border-radius:60% 0 0 0;background:radial-gradient(ellipse at 55% 40%,#3f7a2e,#234d1c 70%,#6b5e48)}
  .scene--whisk{top:270px;height:173px;background:radial-gradient(ellipse at 45% 40%,#6d6455 0%,#3c3833 60%,var(--night) 100%)}
  .scene--leaves{top:230px;height:130px;background:radial-gradient(ellipse at 60% 55%,#3e9a3a 0%,#6fae4b 45%,rgba(243,244,241,0) 80%)}
  .scene--powder{left:140px;top:300px;width:160px;height:70px;border-radius:50% 50% 10% 10%;background:radial-gradient(ellipse at 50% 60%,#b4c563,#8fa544 70%,rgba(143,165,68,0))}

  .pure{position:absolute;font-family:"Oswald",sans-serif;font-weight:600;line-height:1;color:var(--leaf-deep);transform:rotate(-90deg);transform-origin:left top;letter-spacing:1px;white-space:nowrap}
  .rule{position:absolute;width:2px;background:var(--ink)}

  .title-classic{position:absolute;left:80px;top:126px;font-family:"Alfa Slab One",serif;line-height:1.12;color:var(--ink)}
  .title-classic .l1{font-size:23px}
  .title-classic .l2{font-size:28px;color:var(--leaf-deep)}
  .title-classic .l3{font-size:28px}

  .title-night{position:absolute;top:118px;width:100%;text-align:center;font-family:"Cinzel",serif;color:var(--cream)}
  .title-night .l1{font-size:17px;line-height:20px;font-weight:600;letter-spacing:1px}
  .title-night .l2{font-size:42px;line-height:44px;font-weight:700;letter-spacing:6px}
  .title-night .l3{font-size:17px;line-height:22px;font-weight:700;color:var(--leaf)}

  .title-modern{position:absolute;left:48px;top:126px;font-family:"Oswald",sans-serif;line-height:1}
  .title-modern .l1{font-size:20px;line-height:24px;letter-spacing:4px;color:var(--ink);font-weight:500}
  .title-modern .l2{font-size:44px;line-height:46px;color:var(--ink);font-weight:500;margin-left:38px}
  .title-modern .l3{font-size:44px;line-height:46px;color:var(--leaf-deep);font-weight:500;margin-left:38px}

  .badge{position:absolute;width:52px;height:52px;border-radius:50%;background:var(--badge);border:3px solid var(--badge-ring)}
  .badge--light{background:var(--badge-ring);border-color:var(--leaf)}

  .benefits{position:absolute;list-style:none;font-style:italic;font-weight:700;font-size:8.5px;line-height:11px;color:#fff}
  .benefits li{display:flex;align-items:center;gap:3px}
  .benefits svg{width:9px;height:8px;flex:none}
  .benefits--dark{color:var(--leaf-deep)}

  .net{position:absolute;font-style:italic;font-weight:700;font-size:9.5px;line-height:11px;color:#fff}
  .net--dark{color:var(--ink)}
  .label--night .net{color:var(--cream)}
</style>
</head>
<body>

<section class="label label--classic">
  <div class="pattern-zone"></div>
  <div class="scene scene--hills" role="img" aria-label="Misty green tea plantation hills"></div>
  <div class="brand"><span class="brand__dot"></span><span class="brand__name">Verdant Crest</span></div>
  <div class="pure" style="left:38px;top:220px;font-size:18px">100%PURE</div>
  <div class="rule" style="left:66px;top:130px;height:92px"></div>
  <div class="title-classic"><div class="l1">Ceremonial</div><div class="l2">MATCHA</div><div class="l3">Organic</div></div>
  <div class="badge badge--light" style="left:41px;top:234px"></div>
  <div class="badge" style="left:41px;top:302px"></div>
  <ul class="benefits" style="left:108px;top:262px">
    <li><svg viewBox="0 0 9 8"><path d="M1 4l2.5 3L8 1" stroke="currentColor" stroke-width="1.8" fill="none"/></svg>Enhanced Focus &amp; Memory</li>
    <li><svg viewBox="0 0 9 8"><path d="M1 4l2.5 3L8 1" stroke="currentColor" stroke-width="1.8" fill="none"/></svg>Flat Blocker &amp; Calorie Burner</li>
    <li><svg viewBox="0 0 9 8"><path d="M1 4l2.5 3L8 1" stroke="currentColor" stroke-width="1.8" fill="none"/></svg>Stimulates Metabolism</li>
    <li><svg viewBox="0 0 9 8"><path d="M1 4l2.5 3L8 1" stroke="currentColor" stroke-width="1.8" fill="none"/></svg>Over 1300 Antioxidants</li>
    <li><svg viewBox="0 0 9 8"><path d="M1 4l2.5 3L8 1" stroke="currentColor" stroke-width="1.8" fill="none"/></svg>Great for Baking</li>
  </ul>
  <div class="scene scene--bowl" role="img" aria-label="Wooden bowl heaped with matcha powder"></div>
  <div class="net" style="left:136px;top:413px">Net wet 4 oz<br>(113 g)</div>
</section>

<section class="label label--night">
  <div class="pattern-zone"></div>
  <div class="brand"><span class="brand__dot"></span><span class="brand__name">Verdant Crest</span></div>
  <div class="title-night"><div class="l1">CEREMONIAL</div><div class="l2">MATCHA</div><div class="l3">ORGANIC / 100% PURE</div></div>
  <div class="scene scene--whisk" role="img" aria-label="Bamboo whisk with bowls of matcha powder"></div>
  <div class="badge" style="left:20px;top:232px"></div>
  <div class="badge badge--light" style="left:222px;top:214px"></div>
  <ul class="benefits" style="left:36px;top:355px">
    <li><svg viewBox="0 0 9 8"><path d="M1 4l2.5 3L8 1" stroke="currentColor" stroke-width="1.8" fill="none"/></svg>Enhanced Focus &amp; Memory</li>
    <li><svg viewBox="0 0 9 8"><path d="M1 4l2.5 3L8 1" stroke="currentColor" stroke-width="1.8" fill="none"/></svg>Flat Blocker &amp; Calorie Burner</li>
    <li><svg viewBox="0 0 9 8"><path d="M1 4l2.5 3L8 1" stroke="currentColor" stroke-width="1.8" fill="none"/></svg>Stimulates Metabolism</li>
    <li><svg viewBox="0 0 9 8"><path d="M1 4l2.5 3L8 1" stroke="currentColor" stroke-width="1.8" fill="none"/></svg>Over 1300 Antioxidants</li>
    <li><svg viewBox="0 0 9 8"><path d="M1 4l2.5 3L8 1" stroke="currentColor" stroke-width="1.8" fill="none"/></svg>Great for Baking</li>
  </ul>
  <div class="net" style="left:40px;top:414px">Net wet 4 oz<br>(113 g)</div>
</section>

<section class="label label--modern">
  <div class="pattern-zone"></div>
  <div class="scene scene--hills" style="top:200px;height:160px;background:linear-gradient(rgba(243,244,241,0),var(--field) 35%,rgba(243,244,241,0.2))" role="img" aria-label="Green tea fields"></div>
  <div class="brand"><span class="brand__dot"></span><span class="brand__name">Verdant Crest</span></div>
  <div class="pure" style="left:50px;top:238px;font-size:19px">100%PURE</div>
  <div class="rule" style="left:78px;top:152px;height:88px"></div>
  <div class="title-modern"><div class="l1">CEREMONIAL</div><div class="l2">ORGANIC</div><div class="l3">MATCHA</div></div>
  <div class="scene scene--leaves" role="img" aria-label="Fresh green tea leaves"></div>
  <div class="scene scene--powder" role="img" aria-label="Pile of light green matcha powder"></div>
  <div class="badge" style="left:55px;top:246px"></div>
  <div class="badge badge--light" style="left:203px;top:250px"></div>
  <ul class="benefits benefits--dark" style="left:32px;top:380px">
    <li><svg viewBox="0 0 9 8"><path d="M1 4l2.5 3L8 1" stroke="currentColor" stroke-width="1.8" fill="none"/></svg>Enhanced Focus &amp; Memory</li>
    <li><svg viewBox="0 0 9 8"><path d="M1 4l2.5 3L8 1" stroke="currentColor" stroke-width="1.8" fill="none"/></svg>Flat Blocker &amp; Calorie Burner</li>
    <li><svg viewBox="0 0 9 8"><path d="M1 4l2.5 3L8 1" stroke="currentColor" stroke-width="1.8" fill="none"/></svg>Stimulates Metabolism</li>
    <li><svg viewBox="0 0 9 8"><path d="M1 4l2.5 3L8 1" stroke="currentColor" stroke-width="1.8" fill="none"/></svg>Over 1300 Antioxidants</li>
    <li><svg viewBox="0 0 9 8"><path d="M1 4l2.5 3L8 1" stroke="currentColor" stroke-width="1.8" fill="none"/></svg>Great for Baking</li>
  </ul>
  <div class="net net--dark" style="left:197px;top:413px">Net wet 4 oz<br>(113 g)</div>
</section>

</body>
</html>
```